Bright Harbor Counseling Letterhead for hip modern business

I would like some ombre use of the colors in the logo hip letterhead that incorporates logo colors and feel, needs to connect with young professionals and college students. i need to be able to write letters to schools to excuse absences as well. i like color blocks on one side preferably using colors from the attached logo design.

Target Market(s)

high income young people, young adults and college students

Industry/Entity Type

mental health

Font styles to use
Serif
Sans Serif

Colors
0054AA
0677BA
7BADD7
CADEEF
E8F1F8
0094D4
00A9DD
6FCCEA
C7EBF8
E9F6FB
00AB8E
00BBA5
67D7C9
C6EFE9
E9F9F6
59FF00
82FF00
B8FF75
E3FFCB
F4FFEA
A7469A
B969AE
D3A5CF
EDDBEB
F8F0F9
6B429C
8869AF
B7A5CE
E3DAEB
F3F0F8

Requirements
Must have
• a modern hip feel, somewhat color

```html
<!DOCTYPE html>
<html lang="en">
<head>
<meta charset="utf-8">
<title>Bright Harbor Counseling Letterhead</title>
<link href="https://fonts.googleapis.com/css2?family=Open+Sans:wght@300;400&family=Lato:wght@400&display=swap" rel="stylesheet">
<style>
  :root {
    --ink: #1a1a1a;
    --body: #444444;
    --muted: #555555;
    --rule: #333333;
    --teal: #5cc2b8;
    --band: #050708;
    --accent: #a7469a;
    --paper: #ffffff;
    --sig: #e6e6e6;
  }
  * { margin: 0; padding: 0; box-sizing: border-box; }
  html, body { width: 1040px; height: 1200px; overflow: hidden; background: var(--paper); }
  .sheet { position: relative; width: 1040px; height: 1200px; background: var(--paper); font-family: "Open Sans", Arial, sans-serif; color: var(--body); }

  .brand { position: absolute; left: 98px; top: 84px; display: flex; align-items: center; gap: 12px; }
  .brand-dot { width: 16px; height: 16px; border-radius: 50%; background: var(--accent); }
  .brand-name { font-weight: 300; font-size: 31px; color: var(--ink); letter-spacing: 0.3px; }

  .contact { position: absolute; left: 700px; top: 38px; height: 66px; border-left: 1.5px solid var(--rule); padding-left: 18px; font-family: "Lato", Arial, sans-serif; font-size: 17.5px; color: var(--ink); }
  .contact li { list-style: none; display: flex; align-items: center; gap: 12px; height: 22px; }
  .contact svg { width: 16px; height: 16px; flex: none; }

  .meta { position: absolute; left: 98px; font-size: 15px; line-height: 18px; color: var(--muted); }
  .date { top: 234px; }
  .recipient { top: 270px; }
  .salutation { top: 374px; }

  .letter-body { position: absolute; left: 98px; top: 426px; width: 840px; font-size: 15px; line-height: 27px; color: var(--body); text-align: justify; }
  .letter-body p + p { margin-top: 27px; }

  .closing { position: absolute; left: 98px; top: 830px; font-size: 15px; color: var(--muted); }
  .signature { position: absolute; left: 98px; top: 872px; width: 225px; height: 26px; background: var(--sig); }
  .signer { position: absolute; left: 98px; top: 909px; font-size: 19px; color: var(--ink); }
  .signer-title { position: absolute; left: 98px; top: 942px; font-size: 15px; color: var(--muted); }

  .footer-band { position: absolute; left: 0; top: 1040px; width: 1040px; height: 160px; background: linear-gradient(to bottom, var(--teal) 0px, var(--band) 48px, var(--band) 100%); }
  .footer-address { position: absolute; right: 89px; top: 1127px; font-family: "Lato", Arial, sans-serif; font-size: 17.5px; color: var(--paper); }
</style>
</head>
<body>
<main class="sheet">
  <header>
    <div class="brand">
      <span class="brand-dot"></span>
      <span class="brand-name">Bright Harbor Counseling</span>
    </div>
    <ul class="contact">
      <li>
        <svg viewBox="0 0 16 16" aria-hidden="true"><path d="M1 5c0-2 3-3 7-3s7 1 7 3v1h-4V5H5v1H1z" fill="#111"/><path d="M4 7h8l2 6H2z" fill="#111"/></svg>
        044-555 210 734
      </li>
      <li>
        <svg viewBox="0 0 16 16" aria-hidden="true"><rect x="1" y="3" width="14" height="10" fill="#111"/><path d="M1 3l7 6 7-6M1 13l5-5M15 13l-5-5" stroke="#fff" stroke-width="1.3" fill="none"/></svg>
        hello@brightharbor.example
      </li>
      <li>
        <svg viewBox="0 0 16 16" aria-hidden="true"><circle cx="8" cy="8" r="7" fill="#111"/><path d="M4 5c2 0 3 1 3 3s-2 2-2 4M10 3c0 2 2 2 3 3M9 10c1 0 2 1 2 3" stroke="#fff" stroke-width="1.3" fill="none"/></svg>
        www.brightharbor.example
      </li>
    </ul>
  </header>

  <p class="meta date">Issuing Date: May 5, 2018</p>
  <p class="meta recipient">Name Of Employee Mr. XYZABC<br>Address of Employee<br>Address Line 2 etc..</p>
  <p class="meta salutation">Dear Mr.XYZABC</p>

  <section class="letter-body">
    <p>Lorem Ipsum has been the industry's standard dummy text ever since the 1500s, when an unknown printer took a galley of type and scrambled it to make a type specimen book. It has survived not only five centuries, but also the leap into electronic typesetting, remaining essentially unchanged. It was popularised in the 1960s with the release of Quillmark sheets containing Lorem Ipsum passages, and more recently with desktop publishing software like Pressline Studio including versions of Lorem Ipsum.</p>
    <p>Lorem Ipsum is simply dummy text of the printing and typesetting industry. Lorem Ipsum has been the industry's standard dummy text ever since the 1500s, when an unknown printer took a galley of type and scrambled it to make a type specimen book.</p>
    <p>It has survived not only five centuries, but also the leap into electronic typesetting, remaining essentially unchanged. It was popularised in the 1960s with the release of Quillmark sheets containing Lorem IpsumIpsum passages.</p>
  </section>

  <p class="closing">Yours Sincerely</p>
  <div class="signature" role="img" aria-label="Handwritten signature of Daniel Reeve"></div>
  <p class="signer">Daniel Reeve</p>
  <p class="signer-title">Managing Director</p>

  <footer>
    <div class="footer-band" role="img" aria-label="Decorative teal and black wave band along the foot of the page"></div>
    <p class="footer-address">18 Quayside Lane, Portmere, 30918</p>
  </footer>
</main>
</body>
</html>
```